New business card/stationary for a consulting company

I am looking for a clean and very professional looking business card for my consulting company as well as corresponding stationary. I am uploading our logo. I like simple and powerful for the feel. No graphics but I am open on everything else. Below is my contact information but would like the final to be in a version I can add my employees information into and print. Thank you.

Daniel Whitcombe
dan@ferncliffadvisory.com
2870 North 9th Avenue, Summit Floor, Elm Ridge, Illinois 60531
www.ferncliffadvisory.com

Industry/Entity Type

Consulting

Contact Information for Business Card

Daniel Whitcombe
dan@ferncliffadvisory.com
www.ferncliffadvisory.com

Font styles to use
Serif
Sans Serif

Requirements
Must have
• Our logo and the business card details.
Nice to have
• our website www.ferncliffadvisory.com

```html
<!DOCTYPE html>
<html lang="en">
<head>
<meta charset="utf-8">
<title>Ferncliff Advisory – Business Card</title>
<link rel="stylesheet" href="https://fonts.googleapis.com/css2?family=Marcellus&family=Roboto:wght@400&display=swap">
<style>
  :root {
    --navy: #122a5b;
    --white: #ffffff;
    --paper: #f4f4f4;
    --paper-shade: #e9e9e9;
    --backdrop: #e4e4e4;
    --ink: #2b2b2b;
  }
  * { margin: 0; padding: 0; box-sizing: border-box; }
  html, body { width: 1200px; height: 576px; overflow: hidden; }
  body { background: var(--backdrop); position: relative; }

  .card {
    position: absolute;
    width: 484px;
    height: 292px;
    border-radius: 12px;
  }
  .card-front { left: 82px; top: 139px; background: var(--navy); }
  .card-back {
    left: 602px; top: 138px;
    background: linear-gradient(180deg, var(--paper) 0%, var(--paper-shade) 100%);
  }

  .brand-mark { display: block; width: 40px; height: 40px; }
  .card-front .brand-mark { background: var(--white); }
  .card-back .brand-mark { background: var(--navy); }

  .brand-name {
    font-family: "Marcellus", serif;
    font-weight: 400;
    text-transform: uppercase;
    white-space: nowrap;
  }

  .front-brand {
    position: absolute;
    left: 0; right: 0; top: 104px;
    display: flex; flex-direction: column; align-items: center; gap: 24px;
  }
  .front-brand .brand-name { color: var(--white); font-size: 26px; letter-spacing: 1px; }

  .back-brand {
    position: absolute;
    left: 208px; width: 250px; top: 40px;
    display: flex; flex-direction: column; align-items: center; gap: 20px;
  }
  .back-brand .brand-name { color: var(--navy); font-size: 20px; letter-spacing: 0.6px; }

  .contact { position: absolute; left: 23px; top: 202px; }
  .contact-name {
    font-family: "Marcellus", serif;
    color: var(--navy);
    font-size: 18px;
    letter-spacing: 0.8px;
    text-transform: uppercase;
    margin-bottom: 6px;
  }
  .contact-line {
    display: flex; align-items: center; gap: 6px;
    font-family: "Roboto", sans-serif;
    font-size: 12.3px;
    color: var(--ink);
    height: 20px;
    white-space: nowrap;
  }
  .contact-item { display: flex; align-items: center; gap: 5px; }
  .contact-item + .contact-item { margin-left: 4px; }
  .icon { width: 11px; height: 11px; fill: var(--navy); flex: none; }
</style>
</head>
<body>

<section class="card card-front" aria-label="Card front">
  <div class="front-brand">
    <span class="brand-mark"></span>
    <span class="brand-name">Ferncliff Advisory</span>
  </div>
</section>

<section class="card card-back" aria-label="Card back">
  <div class="back-brand">
    <span class="brand-mark"></span>
    <span class="brand-name">Ferncliff Advisory</span>
  </div>

  <div class="contact">
    <p class="contact-name">Daniel Whitcombe</p>
    <div class="contact-line">
      <span class="contact-item">
        <svg class="icon" viewBox="0 0 12 12" aria-hidden="true"><path d="M0 2h12v8H0z M1 3l5 3.5L11 3v-.2H1z" fill-rule="evenodd"/><path d="M0 2.5l6 4 6-4" fill="none" stroke="#f2f2f2" stroke-width="1"/></svg>
        dan@ferncliffadvisory.com
      </span>
      <span class="contact-item">
        <svg class="icon" viewBox="0 0 12 12" aria-hidden="true"><circle cx="6" cy="6" r="5.5"/><path d="M0.5 6h11M6 0.5v11M3.2 1.5c-1.6 3-1.6 6 0 9M8.8 1.5c1.6 3 1.6 6 0 9" stroke="#f2f2f2" stroke-width="0.8" fill="none"/></svg>
        www.ferncliffadvisory.com
      </span>
    </div>
    <div class="contact-line">
      <span class="contact-item">
        <svg class="icon" viewBox="0 0 12 12" aria-hidden="true"><path d="M6 0a4 4 0 0 0-4 4c0 3 4 8 4 8s4-5 4-8a4 4 0 0 0-4-4zm0 5.6A1.6 1.6 0 1 1 6 2.4a1.6 1.6 0 0 1 0 3.2z"/></svg>
        2870 North 9th Avenue, Summit Floor, Elm Ridge, Illinois 60531
      </span>
    </div>
  </div>
</section>

</body>
</html>
```